Create a step-by-step donors pamphlet for VELTO church

I am looking to get a professionally design pamphlet that gives our donors easy steps to set up reoccurring donation through our give platform.

The ideal design should look professional and creative. No templates or weak AIs.

I've provided church logos and a text file which contains the content of the pamphlet we are trying to make.

Font styles to use
Sans Serif

Requirements
Must have
• Good branding

```html
<!DOCTYPE html>
<html lang="en">
<head>
<meta charset="utf-8">
<title>VELTO – Recurring Giving Pamphlet</title>
<link rel="stylesheet" href="https://fonts.googleapis.com/css2?family=Archivo:wght@400;600;800&display=swap">
<style>
  :root{
    --ink:#1b1a1a;
    --flame:#e8772a;
    --paper:#ffffff;
    --text-light:#e6e6e6;
    --text-muted:#bdbdbd;
    --text-dark:#2a2a2a;
    --glass-a:#7a3b2e;
    --glass-b:#3d5a78;
    --glass-c:#b0814a;
    --page:#ececec;
  }
  *{box-sizing:border-box;margin:0;padding:0}
  html,body{width:1200px;height:655px;overflow:hidden;background:var(--page)}
  body{font-family:"Archivo",Arial,sans-serif}
  .pamphlet{position:relative;width:1200px;height:655px;display:flex}
  .panel{position:relative;height:100%;overflow:hidden}

  /* Brand name: plain text, one colour, one weight */
  .brand-name{display:flex;align-items:center;justify-content:center;gap:10px;
    font-family:"Archivo",Arial,sans-serif;font-weight:800;color:var(--paper);letter-spacing:1px;line-height:1}
  .brand-name .brand-dot{width:12px;height:12px;border-radius:50%;background:var(--flame)}
  .motto{font-family:"Archivo",Arial,sans-serif;font-weight:400;color:var(--text-muted);letter-spacing:.2px}

  /* Panel 1 – cover */
  .cover{width:284px;background:var(--ink);color:var(--paper);text-align:center}
  .cover-title{position:absolute;top:30px;left:20px;right:20px;font-weight:800;font-size:26px;line-height:1.22;letter-spacing:.5px}
  .cover-art{position:absolute;top:230px;left:50px;width:180px;height:270px;border-radius:50%;
    background:radial-gradient(ellipse at center,rgba(232,119,42,.45),rgba(232,119,42,.12) 45%,rgba(27,26,26,0) 72%)}
  .cover .brand-name{position:absolute;left:0;right:0;top:520px;font-size:46px}
  .cover .motto{position:absolute;left:0;right:0;top:578px;font-size:14px}

  /* Panel 2 – partner */
  .partner{width:287px;background:var(--paper)}
  .glass-art{position:absolute;left:0;top:0;width:100%;height:302px;
    background:linear-gradient(135deg,var(--glass-a) 0%,var(--glass-b) 40%,var(--glass-c) 70%,var(--glass-b) 100%)}
  .partner-body{position:absolute;top:318px;left:22px;right:18px}
  .partner-heading{color:var(--flame);font-weight:800;font-size:13.5px;text-align:center;line-height:1.35;letter-spacing:.3px}
  .partner-intro{margin-top:14px;font-size:14px;line-height:1.35;color:var(--text-dark);text-align:center}
  .partner-rule{margin:8px auto 0;width:150px;border-top:1px dashed #999}
  .benefits{list-style:none;margin-top:12px}
  .benefits li{display:flex;gap:8px;font-size:14px;line-height:1.32;color:var(--text-dark);margin-bottom:14px}
  .benefits svg{flex:none;margin-top:2px}

  /* Panel 3 – steps */
  .steps{width:303px;background:var(--ink);color:var(--text-light)}
  .steps-top{position:absolute;top:36px;left:12px;right:12px}
  .steps p{font-size:12.5px;line-height:1.4}
  .step-title{color:var(--flame);font-weight:800;font-size:12.5px;letter-spacing:.3px;margin-top:16px;text-transform:uppercase}
  .steps-band{position:absolute;top:283px;left:0;right:0;height:106px;background:var(--paper);
    text-align:center;padding:18px 14px 0}
  .steps-band .step-title{margin-top:0}
  .steps-band p{color:var(--text-dark)}
  .steps-bottom{position:absolute;top:405px;left:12px;right:12px}
  .steps-bottom .step-title{margin-top:0}
  .two-col{display:grid;grid-template-columns:1fr 1fr;gap:10px;margin-top:6px;margin-bottom:16px}
  .two-col p{font-size:11.5px}
  .fold-line{position:absolute;top:0;bottom:0;right:0;border-right:1px dashed #555}

  /* Panel 4 – back */
  .back{flex:1;background:var(--ink);color:var(--paper);text-align:center}
  .window-art{position:absolute;top:12px;left:87px;width:164px;height:290px;border-radius:82px 82px 6px 6px;
    background:linear-gradient(180deg,var(--glass-b),var(--glass-a) 60%,#4a4848)}
  .back .brand-top{position:absolute;top:140px;left:0;right:0;font-size:50px}
  .back .motto-top{position:absolute;top:200px;left:0;right:0;font-size:15px;color:var(--text-light)}
  .back-band{position:absolute;top:304px;left:0;right:0;height:89px;background:var(--paper);color:var(--text-dark);
    text-align:left;padding:14px 14px 0;font-size:13px;line-height:1.4}
  .back .brand-bottom{position:absolute;top:450px;left:0;right:0;font-size:42px}
  .back .motto-bottom{position:absolute;top:504px;left:0;right:0;font-size:13px}
  .contact-box{position:absolute;left:24px;right:30px;top:556px;height:66px;border:1.5px solid var(--flame);border-radius:6px;
    font-style:normal;font-size:12px;line-height:1.45;padding:7px 8px;color:var(--text-light)}
</style>
</head>
<body>
<main class="pamphlet">

  <section class="panel cover">
    <h1 class="cover-title">ARE YOU A RECURRING DONOR YET?</h1>
    <div class="cover-art" role="img" aria-label="Orange flame rising through dark smoke"></div>
    <div class="brand-name"><span class="brand-dot"></span>VELTO</div>
    <p class="motto">A voice to all nations</p>
  </section>

  <section class="panel partner">
    <div class="glass-art" role="img" aria-label="Stained glass church windows with a white dove in flight"></div>
    <div class="partner-body">
      <h2 class="partner-heading">PARTNER WITH VELTO<br>IN BUILDING THE KINGDOM</h2>
      <p class="partner-intro">Your faithful gift each month helps us reach more people, serve our city and share hope.</p>
      <div class="partner-rule"></div>
      <ul class="benefits">
        <li>
          <svg width="18" height="18" viewBox="0 0 18 18"><circle cx="9" cy="9" r="8" fill="none" stroke="#e8772a" stroke-width="2"/><path d="M5 9l3 3 5-6" fill="none" stroke="#e8772a" stroke-width="2"/></svg>
          <span>Steady giving that fuels the mission and outreach of our church.</span>
        </li>
        <li>
          <svg width="18" height="18" viewBox="0 0 18 18"><circle cx="9" cy="9" r="8" fill="none" stroke="#e8772a" stroke-width="2"/><path d="M5 9l3 3 5-6" fill="none" stroke="#e8772a" stroke-width="2"/></svg>
          <span>One simple setup, a lasting gift to our community.</span>
        </li>
      </ul>
    </div>
  </section>

  <section class="panel steps">
    <div class="steps-top">
      <p>Giving every month is easy. Follow these short steps to set up a recurring gift through our online giving page.</p>
      <h3 class="step-title">Set up a recurring donation today</h3>
      <p>1. Open our website and tap the Give button at the top of any page.</p>
      <h3 class="step-title">Once you're on the giving page</h3>
      <p>2. Choose your fund, enter an amount and pick how often to give.</p>
    </div>
    <div class="steps-band">
      <h3 class="step-title">Set up a recurring gift now</h3>
      <p>Select monthly or weekly, add your card or bank details, then confirm on the giving page.</p>
    </div>
    <div class="steps-bottom">
      <h3 class="step-title">3. Once you're on the giving sheet</h3>
      <div class="two-col">
        <p>Pick your start date and review each detail.</p>
        <p>Save your gift and watch for a receipt.</p>
      </div>
      <h3 class="step-title">4. Once you're on the confirm page</h3>
      <div class="two-col">
        <p>Manage or change your gift at any time.</p>
        <p>Thank you for giving with us.</p>
      </div>
    </div>
    <div class="fold-line"></div>
  </section>

  <section class="panel back">
    <div class="window-art" role="img" aria-label="Illustrated stained glass arched window with doves"></div>
    <div class="brand-name brand-top">VELTO</div>
    <p class="motto motto-top">A voice to all nations</p>
    <div class="back-band">Do you have a heart for this church? Partner with us and help carry the message of hope to our city all through the year.</div>
    <div class="brand-name brand-bottom">VELTO</div>
    <p class="motto motto-bottom">A voice to all nations</p>
    <address class="contact-box">www.veltochurch.org<br>give@veltochurch.org<br>(555) 014-2300 · 12 Harbor Lane</address>
  </section>

</main>
</body>
</html>
```